Lawn sign for construction company

Would like this to be a very clean and high end design for luxury homes. We need a yard sign designed that includes the company logo, website, phone number and major service offerings (residential and commercial renovations and maintenance)
The company website is brackwellbuilders.com all other contact info is in the attachments
Target Market(s)
Luxury home owners and business owners
Industry/Entity Type
Construction/Home Improvement
Font styles to use
Other font styles liked:
- See company logo and other graphics included for title text fonts. All other fonts can be standard sans serif.
Colors
0054AA
0677BA
7BADD7
CADEEF
E8F1F8
Requirements
Must have
- Clean, easy to read design, would like 2 sided sign. A main sign side and back side which states “free estimates, and includes the website and phone number. Must also match the color scheme of the provided logo and other company images. Dark Navy blue primary color, gray secondary color, and orange as an accent color.
Nice to have
- 2nd sign side very simple design
Should not have
- Too many graphics limit to 1-3 colors

```html
<!DOCTYPE html>
<html lang="en">
<head>
<meta charset="UTF-8">
<title>Brackwell Builders – Yard Sign</title>
<link href="https://fonts.googleapis.com/css2?family=Saira+Stencil+One&family=Montserrat:wght@600;700&display=swap" rel="stylesheet">
<style>
  :root {
    --backdrop: #b5b4b5;
    --panel-dark: #cbcbcb;
    --panel-light: #dcdcdc;
    --navy: #131884;
    --navy-deep: #0c1170;
    --orange: #ec7a0b;
    --gray: #666666;
    --white: #ffffff;
  }
  * { margin: 0; padding: 0; box-sizing: border-box; }
  html, body { width: 1200px; height: 1200px; overflow: hidden; }
  body { background: var(--backdrop); position: relative; }

  .sign {
    position: absolute;
    left: 227px;
    width: 746px;
    height: 497px;
    background: linear-gradient(to bottom right, var(--panel-dark) 50%, var(--panel-light) 50%);
  }
  .sign--front { top: 73px; }
  .sign--back { top: 631px; }

  .sign__frame {
    position: absolute;
    left: 16px; top: 14px; right: 15px; bottom: 13px;
    border: 1.5px solid var(--navy-deep);
  }

  .brand {
    position: absolute;
    left: 0; right: 0;
    display: flex; justify-content: center; align-items: center; gap: 14px;
    font-family: "Saira Stencil One", sans-serif;
    color: var(--orange);
    font-size: 54px;
    line-height: 1;
  }
  .brand__mark { width: 22px; height: 22px; background: var(--orange); }
  .sign--front .brand { top: 122px; }
  .sign--back .brand { top: 148px; }

  .headline {
    position: absolute;
    top: 290px; left: 0; right: 0;
    text-align: center;
    font-family: "Saira Stencil One", sans-serif;
    font-size: 82px;
    line-height: 1;
    color: var(--navy);
    letter-spacing: 1px;
  }

  .phone {
    position: absolute;
    top: 366px; left: 0; right: 0;
    display: flex; justify-content: center; align-items: center; gap: 8px;
    font-family: "Montserrat", sans-serif;
    font-weight: 700;
    font-size: 56px;
    line-height: 1;
    color: var(--gray);
  }
  .phone__icon { width: 44px; height: 44px; }

  .web-pill {
    position: absolute;
    display: flex; justify-content: center; align-items: center;
    border-radius: 12px;
  }
  .web-pill--front {
    left: 116px; top: 427px; width: 511px; height: 41px;
    background: var(--orange);
    color: var(--navy-deep);
    font-family: "Montserrat", sans-serif;
    font-weight: 700;
    font-size: 29px;
  }
  .web-pill--back {
    left: 65px; top: 423px; width: 612px; height: 49px;
    background: var(--navy-deep);
    color: var(--orange);
    font-family: "Saira Stencil One", sans-serif;
    font-size: 40px;
    letter-spacing: 1px;
  }

  .services {
    position: absolute;
    top: 338px; left: 0; right: 0;
    text-align: center;
    font-family: "Saira Stencil One", sans-serif;
    font-size: 33px;
    line-height: 34px;
    color: var(--gray);
  }
  .services__dot {
    display: inline-block;
    width: 13px; height: 13px;
    background: var(--orange);
    margin: 0 6px;
    vertical-align: 5px;
  }
</style>
</head>
<body>
  <section class="sign sign--front">
    <div class="sign__frame"></div>
    <div class="brand"><span class="brand__mark"></span>BRACKWELL BUILDERS</div>
    <h1 class="headline">FREE ESTIMATES</h1>
    <div class="phone">
      <svg class="phone__icon" viewBox="0 0 48 48" aria-hidden="true">
        <path d="M10 8c2-2 5-2 6 0l4 7c1 2 0 4-2 5l-2 1c2 5 6 9 11 11l1-2c1-2 3-3 5-2l7 4c2 1 2 4 0 6l-3 3c-3 3-9 2-17-4S5 22 6 15z" fill="var(--orange)"/>
        <path d="M28 12a10 10 0 0 1 9 9M28 6a16 16 0 0 1 15 15M29 18a4 4 0 0 1 3 3" fill="none" stroke="var(--orange)" stroke-width="2.5" stroke-linecap="round"/>
      </svg>
      800-555-0142
    </div>
    <div class="web-pill web-pill--front">www.brackwellbuilders.com</div>
  </section>

  <section class="sign sign--back">
    <div class="sign__frame"></div>
    <div class="brand"><span class="brand__mark"></span>BRACKWELL BUILDERS</div>
    <p class="services">
      RESIDENTIAL RENOVATIONS<span class="services__dot"></span>COMMERCIAL<br>
      RENOVATIONS<span class="services__dot"></span>MAINTENANCE
    </p>
    <div class="web-pill web-pill--back">www.brackwellbuilders.com</div>
  </section>
</body>
</html>
```